VELMOR Website Design

We need a website designed for our company VELMOR. We are a luxury lifestyle club that will provide benefits and services for our members. The site should be clean & sleek, preferably using black and white (or darker colors). (example sites: stravenhall.example, plinth.example)

Here is a link of a sample page I did using wix. (https://dunmere7.sitehostly.example/mysite) This can be used to get a general idea.

Target Market(s)

Upper Middle Class in the United States

Number of Pages Required

5+ page

Font styles to use
Sans Serif
Other font styles liked:
• Arial (or other similar fonts)

Requirements
Must have
• A clean design that is eye-catching and speaks to our company.
Nice to have
• Ideas for copy.

```html
<!DOCTYPE html>
<html lang="en">
<head>
<meta charset="utf-8">
<title>VELMOR — Apply</title>
<link rel="stylesheet" href="https://fonts.googleapis.com/css2?family=Montserrat:wght@300;400;600&display=swap">
<style>
  :root {
    --bg: #080c18;
    --facet-a: #0c1c2c;
    --facet-b: #0d1736;
    --text: #ffffff;
    --muted: #d9dce4;
    --line: #c9ccd4;
    --icon: #b9bcc6;
  }
  * { box-sizing: border-box; margin: 0; padding: 0; }
  html, body { width: 1200px; height: 977px; overflow: hidden; }
  body {
    position: relative;
    background: var(--bg);
    color: var(--text);
    font-family: "Montserrat", Arial, sans-serif;
  }
  .backdrop { position: absolute; inset: 0; width: 1200px; height: 977px; }
  .site-header {
    position: absolute; top: 0; left: 0; width: 1200px; height: 96px;
  }
  .brand {
    position: absolute; left: 150px; top: 30px;
    font-size: 33px; font-weight: 400; letter-spacing: 1.5px;
  }
  .main-nav {
    position: absolute; right: 120px; top: 41px;
    display: flex; gap: 26px;
    font-size: 13px; letter-spacing: 0.6px; color: var(--muted);
  }
  .main-nav .active { color: var(--text); font-weight: 600; }
  .page-title {
    position: absolute; left: 133px; top: 200px;
    font-size: 51px; font-weight: 400; letter-spacing: 0.5px;
  }
  .title-rule {
    position: absolute; left: 162px; top: 269px; width: 72px; height: 1px;
    background: var(--line);
  }
  .intro {
    position: absolute; left: 135px; top: 316px; width: 780px;
    font-size: 15.5px; line-height: 26.5px; letter-spacing: 2.6px;
    font-weight: 400; color: var(--text);
  }
  .form-title {
    position: absolute; left: 133px; top: 428px;
    font-size: 28px; font-weight: 400;
  }
  .interest-form .field {
    position: absolute; left: 135px; width: 270px; height: 35px;
    border: 1px solid var(--line); background: rgba(5, 8, 16, 0.9);
    color: #b8bbc4; font-family: inherit; font-size: 14.5px;
    letter-spacing: 0.8px; padding: 0 16px; line-height: 33px;
  }
  .field-name { top: 489px; }
  .field-email { top: 554px; }
  .field-phone { top: 618px; }
  .apply-button {
    position: absolute; left: 136px; top: 705px; width: 143px; height: 44px;
    border: 2px solid var(--text); border-radius: 22px;
    background: transparent; color: var(--text);
    font-family: inherit; font-size: 14.5px; font-weight: 600;
    text-align: center; line-height: 40px;
  }
  .site-footer {
    position: absolute; left: 0; top: 906px; width: 1200px; text-align: center;
  }
  .footer-label { font-size: 12.5px; font-weight: 600; letter-spacing: 0.3px; }
  .social-list {
    display: flex; justify-content: center; gap: 12px; margin-top: 9px;
  }
  .social-dot {
    width: 15px; height: 15px; border-radius: 50%; background: var(--icon);
  }
</style>
</head>
<body>
  <svg class="backdrop" viewBox="0 0 1200 977" role="img" aria-label="Faceted dark blue geometric background panel">
    <defs>
      <linearGradient id="facetFill" x1="1" y1="0" x2="0.4" y2="1">
        <stop offset="0" stop-color="var(--facet-a)"/>
        <stop offset="1" stop-color="var(--facet-b)"/>
      </linearGradient>
    </defs>
    <polygon points="1000,0 1200,0 1200,977 690,977 497,390" fill="url(#facetFill)"/>
  </svg>

  <header class="site-header">
    <div class="brand">VELMOR</div>
    <nav class="main-nav">
      <span>HOME</span>
      <span class="active">ABOUT</span>
      <span>SERVICES AND BENEFITS</span>
      <span>APPLY</span>
      <span>CONTACT</span>
    </nav>
  </header>

  <main>
    <h1 class="page-title">Apply</h1>
    <div class="title-rule"></div>
    <p class="intro">Hey - Thanks for your interest! We will begin accepting applicants in 2019. In the meantime, simply fill out the indication of interest below and we will be in touch once we begin accepting applications!</p>
    <h2 class="form-title">Indication of Interest</h2>
    <form class="interest-form">
      <div class="field field-name">Full Name</div>
      <div class="field field-email">Email</div>
      <div class="field field-phone">Phone</div>
      <div class="apply-button">Apply</div>
    </form>
  </main>

  <footer class="site-footer">
    <div class="footer-label">CONTACT US</div>
    <div class="social-list" aria-label="Social media links">
      <span class="social-dot"></span>
      <span class="social-dot"></span>
      <span class="social-dot"></span>
      <span class="social-dot"></span>
      <span class="social-dot"></span>
    </div>
  </footer>
</body>
</html>
```